Orthobiologic, StemCell, Bone Marrow Aspirate Device Distributor

We need a wordpress fully functioning website design for an innovative ortho-biologic, Bone Marrow Aspirate Device that extracts stem cells for orthopedic regenerative medical professionals. We also offer state of the art training in there office setting with licensed medical staff, a full service support team, and software for tracking patient outcome over time. We are an innovative company that prides itself on gold standard support. We will have other offerings on our website and would like a spot for "future" products. We would like to see designs that look professional, medical, and convey support, security, science, and innovation. We prefer shades of blue and red/orange. I particularly like the following websites that also sell the same device in order of preference:regenacelltherapy.comhttps://aspire-medical.eu/marrow-cellution/https://www.matrixbiosurgical.com/#emerging-solutions-in-healthcareElite2elite.comI have attached a few pictures of the device for reference

Target Market(s)

Orthopedics, Regenerative medicine doctors, Industry representatives, Hospitals

Industry/Entity Type

Medical Equipment

Coding

Coded - Design and coding required

Colors
3176b5
33a6d7
f37022
ec1f27

Requirements
Must have
• It must be able to have videos which I can supply, email, online ordering, and sfax. I have a domain name Coralweavesolutions.com . It must have a FAQ section which you can obtain some information from https://www.tolvenclinical.com/solutions#resources
• The device is manufactured by Dulmor and this is the link to the product page http://www.dulmor.com/quintadraw
• I am currently working on a custom logo and should be able to supply that in short order. I prefer shades of blue and red.
Nice to have
• I would love to have a graphic video as seen here: please see quinta draw vs bone marrow aspirate concentrate.
• https://www.tolvenclinical.com/solutions#competition
• I would pay considerably more to have something similar if it is at all possible
Should not have
• Nothing specific

```html
<!DOCTYPE html>
<html lang="en">
<head>
<meta charset="utf-8">
<title>Coral Weave Solutions</title>
<link href="https://fonts.googleapis.com/css2?family=Lato:ital,wght@0,400;0,700;0,900;1,400&display=swap" rel="stylesheet">
<style>
:root{
  --orange:#f07022;
  --blue:#3176b5;
  --blue-dark:#2a63a6;
  --teal:#1f5a63;
  --ink:#1e1e1e;
  --text:#444;
  --muted:#8a8a8a;
  --dark:#333;
  --darker:#2c2c2c;
  --white:#fff;
}
*{margin:0;padding:0;box-sizing:border-box}
html,body{width:1200px;height:4288px;overflow:hidden}
body{font-family:'Lato',sans-serif;color:var(--ink);background:var(--white);position:relative}
section,header,footer{position:absolute;left:0;width:1200px}
.abs{position:absolute}
.center{left:0;width:1200px;text-align:center}
.btn{position:absolute;background:var(--orange);color:var(--white);text-transform:uppercase;display:flex;align-items:center;justify-content:center;font-weight:700;box-shadow:0 2px 4px rgba(0,0,0,.15)}

/* header */
.site-header{top:0;height:100px;background:var(--white)}
.brand{left:90px;top:16px;color:var(--orange);font-weight:400}
.brand .name{font-size:33px;line-height:36px;letter-spacing:.5px}
.brand .sub{font-size:16px;letter-spacing:13.5px;margin-top:4px}
.call{right:92px;top:20px;font-size:17px;color:var(--ink);display:flex;align-items:center;gap:8px}
.call b{color:var(--blue);font-weight:700}
.nav{right:92px;top:62px;display:flex;gap:31px;font-size:16px;font-weight:700;text-transform:uppercase}

/* hero */
.hero{top:100px;height:562px;background:radial-gradient(circle at 88% 20%,#3a9a8c 0,#1f5a63 18%,transparent 30%),radial-gradient(circle at 15% 85%,#4a7e86 0,#1d4a55 22%,transparent 38%),radial-gradient(circle at 50% 40%,#3b7c86,#173e4a 75%);}
.hero h1{top:158px;font-size:66px;font-weight:700;color:var(--white);letter-spacing:.5px}
.hero p{top:240px;font-size:26px;color:var(--white)}
.hero .btn{left:488px;top:328px;width:225px;height:55px;font-size:21px;gap:10px;font-weight:400}
.hero .arrow{top:268px}

/* research */
.research{top:662px;height:596px}
h2.title{position:absolute;left:0;width:1200px;text-align:center;font-size:31px;font-weight:400;text-transform:uppercase;letter-spacing:.3px}
.hex-card{position:absolute;width:296px;height:258px;top:167px}
.hex-card svg.shape{position:absolute;left:0;top:0}
.hex-card .body{position:absolute;left:40px;width:216px;text-align:center}
.hex-card h3{font-size:20px;font-weight:400;line-height:28px;text-transform:uppercase}
.hex-card p{font-size:13px;line-height:25px;color:var(--text)}
.hex-card.active h3,.hex-card.active p{color:var(--white)}
.dots{top:478px;left:563px;display:flex;gap:12px}
.dots span{width:15px;height:15px;border-radius:50%;border:2px solid #999}
.dots span.on{background:var(--orange);border-color:var(--orange)}

/* welcome */
.welcome{top:1258px;height:439px;background:radial-gradient(circle at 8% 25%,#5a8fd0 0,transparent 18%),radial-gradient(circle at 92% 80%,#5a8fd0 0,transparent 20%),linear-gradient(180deg,#3a7fc4,#2f6fb6)}
.welcome h2.title{top:95px;color:var(--white)}
.welcome p{position:absolute;left:140px;width:920px;top:158px;text-align:center;font-size:15px;line-height:29px;color:var(--white)}
.welcome .btn{top:282px;height:54px;font-size:20px;font-weight:400}

/* future */
.future{top:1697px;height:616px}
.product{position:absolute;top:178px;width:316px;height:275px}
.product .label{position:absolute;top:300px;left:0;width:316px;text-align:center;font-size:24px}
.product .rule{position:absolute;top:331px;left:79px;width:158px;height:3px;background:var(--blue)}

/* team */
.team{top:2313px;height:732px;background:linear-gradient(135deg,#ea6c24 0%,#e97028 35%,#9a6f8a 62%,#3b76b8 85%,#3176b5 100%)}
.team h2.title{top:93px;color:var(--white)}
.member{position:absolute;top:166px;width:260px;text-align:center;color:var(--white)}
.member .photo{width:186px;height:186px;border-radius:50%;margin:0 auto;background:radial-gradient(circle at 50% 35%,#f4f4f4,#d9dfe6 70%,#bfc8d2)}
.member h4{font-size:18px;font-weight:400;margin-top:17px}
.member .stars{display:flex;justify-content:center;gap:6px;margin-top:8px}
.member p{font-size:15px;line-height:27px;margin-top:6px}
.member em{display:block;font-size:12px;margin-top:6px}
.team .btn{left:474px;top:582px;width:252px;height:46px;font-size:16px;font-weight:400}

/* faq */
.faq{top:3045px;height:832px}
.faq h2.title{top:97px}
.faq-item{position:absolute;left:165px;width:870px;height:133px;background:var(--white);box-shadow:0 2px 14px rgba(0,0,0,.12);padding:30px 40px}
.faq-item h5{font-size:18px;font-weight:400}
.faq-item p{font-size:14px;line-height:24px;color:var(--muted);margin-top:12px;width:680px}
.faq .btn{left:519px;top:674px;width:160px;height:52px;font-size:18px;font-weight:400}

/* newsletter */
.newsletter{top:3877px;height:150px;background:var(--dark);border-bottom:1px solid #4a4a4a}
.newsletter h6{left:91px;top:55px;font-size:19px;font-weight:700;color:var(--white);text-transform:uppercase}
.newsletter .sub{left:91px;top:84px;font-size:12px;color:#ddd;text-transform:uppercase}
.newsletter .field{left:780px;top:52px;width:280px;height:48px;background:var(--white);font-size:12px;color:#999;padding:16px 19px}
.newsletter .send{left:1060px;top:52px;width:51px;height:48px;background:var(--orange);display:flex;align-items:center;justify-content:center}

/* footer */
.site-footer{top:4027px;height:261px;background:var(--dark);color:var(--white)}
.pin{left:78px;top:37px;width:38px;height:38px;border-radius:50%;background:var(--orange);display:flex;align-items:center;justify-content:center}
.address{left:131px;top:48px;font-size:11px;line-height:32px;text-transform:uppercase}
.foot-nav{right:89px;top:77px;display:flex;gap:29px;font-size:12px;text-transform:uppercase}
.social{right:89px;top:118px;display:flex;gap:12px}
.social span{width:34px;height:34px;border-radius:50%;border:1.5px solid var(--white)}
.copy{top:236px;font-size:11px;color:#ddd}
</style>
</head>
<body>

<header class="site-header">
  <div class="abs brand">
    <div class="name">CORAL WEAVE</div>
    <div class="sub">SOLUTIONS</div>
  </div>
  <div class="abs call">
    <svg width="16" height="16" viewBox="0 0 24 24"><path fill="#3176b5" d="M6.6 10.8a15.1 15.1 0 0 0 6.6 6.6l2.2-2.2c.3-.3.7-.4 1-.2 1.1.4 2.3.6 3.6.6.6 0 1 .4 1 1V20c0 .6-.4 1-1 1A17 17 0 0 1 3 4c0-.6.4-1 1-1h3.5c.6 0 1 .4 1 1 0 1.3.2 2.5.6 3.6.1.3 0 .7-.2 1z"/></svg>
    <b>CALL US :</b> +1 555 210 3388
  </div>
  <nav class="abs nav">
    <span>Home</span><span>Products</span><span>Providers</span><span>Resources</span><span>Distributors</span><span>FAQ</span><span>Contact</span>
  </nav>
</header>

<section class="hero" role="img" aria-label="Close-up of floating stem cells in teal tones">
  <h1 class="abs center">CORAL WEAVE SOLUTION</h1>
  <p class="abs center">Providing innovative and cost effective orthobiologic medical solutions</p>
  <div class="btn"><svg width="16" height="18" viewBox="0 0 16 18"><path d="M0 0l16 9-16 9z" fill="#fff"/></svg>WATCH VIDEO</div>
  <svg class="abs arrow" style="left:72px" width="16" height="26" viewBox="0 0 16 26"><path d="M13 3L3 13l10 10" stroke="#fff" stroke-width="4" fill="none"/></svg>
  <svg class="abs arrow" style="left:1110px" width="16" height="26" viewBox="0 0 16 26"><path d="M3 3l10 10L3 23" stroke="#fff" stroke-width="4" fill="none"/></svg>
</section>

<section class="research">
  <h2 class="title" style="top:96px">Research Services</h2>
  <svg width="0" height="0" class="abs"><defs><filter id="soft" x="-20%" y="-20%" width="140%" height="140%"><feDropShadow dx="0" dy="2" stdDeviation="7" flood-opacity=".14"/></filter></defs></svg>

  <div class="hex-card" style="left:98px">
    <svg class="shape" width="296" height="258" viewBox="0 0 296 258"><polygon points="74,4 222,4 292,129 222,254 74,254 4,129" fill="#fff" filter="url(#soft)"/></svg>
    <div class="body" style="top:28px">
      <svg width="52" height="52" viewBox="0 0 52 52" style="display:block;margin:0 auto 10px"><circle cx="26" cy="26" r="13" fill="#e06a2c"/><g stroke="#3176b5" stroke-width="2"><path d="M26 5v8M26 39v8M5 26h8M39 26h8M11 11l6 6M35 35l6 6M41 11l-6 6M17 35l-6 6"/></g></svg>
      <h3>Factor Based<br>Therapies</h3>
      <p>Lorem ipsum dolor sit amet, consectetur adipiscing elit, sed do eiusmod temporaliqua.</p>
    </div>
  </div>

  <div class="hex-card active" style="left:453px">
    <svg class="shape" width="296" height="258" viewBox="0 0 296 258"><polygon points="74,4 222,4 292,129 222,254 74,254 4,129" fill="#f07022" filter="url(#soft)"/></svg>
    <div class="body" style="top:28px">
      <svg width="52" height="52" viewBox="0 0 52 52" style="display:block;margin:0 auto 10px"><g fill="none" stroke="#fff" stroke-width="2"><circle cx="26" cy="26" r="12"/><circle cx="22" cy="23" r="3"/><circle cx="30" cy="29" r="3"/><path d="M26 4v10M26 38v10M4 26h10M38 26h10M10 10l7 7M35 35l7 7M42 10l-7 7M17 35l-7 7"/></g></svg>
      <h3>Adipose vs<br>Marrow</h3>
      <p>Lorem ipsum dolor sit amet, consectetur adipiscing elit, sed do eiusmod temporaliqua.</p>
    </div>
  </div>

  <div class="hex-card" style="left:806px">
    <svg class="shape" width="296" height="258" viewBox="0 0 296 258"><polygon points="74,4 222,4 292,129 222,254 74,254 4,129" fill="#fff" filter="url(#soft)"/></svg>
    <div class="body" style="top:28px">
      <svg width="52" height="52" viewBox="0 0 52 52" style="display:block;margin:0 auto 10px"><g fill="none" stroke-width="2"><path d="M14 40l18-18 6 6-18 18h-6z" stroke="#3176b5"/><path d="M36 16l6-6M40 20l4-4" stroke="#3176b5"/><path d="M8 44l6-4" stroke="#e06a2c"/></g><path d="M16 40l10-10 4 4-10 10z" fill="#e06a2c"/></svg>
      <h3>BMA</h3>
      <p>Lorem ipsum dolor sit amet, consectetur adipiscing elit, sed do eiusmod temporaliqua.</p>
    </div>
  </div>

  <div class="abs dots"><span class="on"></span><span></span><span></span></div>
</section>

<section class="welcome">
  <h2 class="title">Welcome to Coral Weave Solutions</h2>
  <p>Lorem ipsum dolor sit amet, consectetur adipiscing elit, sed do eiusmod tempor incididunt ut labore et dolore magna aliqua. Ut enim ad minim veniam, quis nostrud exercitation ullamco laboris nisi ut aliquip ex ea commodo consequat. Duis aute irure dolor in reprehenderit in voluptate velit esse cillum dolore eu fugiat nulla pariatur.</p>
  <div class="btn" style="left:390px;width:196px">Learn More</div>
  <div class="btn" style="left:613px;width:197px">Contact Us</div>
</section>

<section class="future">
  <h2 class="title" style="top:98px">Future Products</h2>
  <div class="product" style="left:90px">
    <svg width="316" height="275" viewBox="0 0 316 275"><polygon points="79,1 237,1 315,137.5 237,274 79,274 1,137.5" fill="#fff" stroke="#bbb" stroke-width="1.2"/><rect role="img" aria-label="Set of bone marrow aspiration needles with blue and green handles" x="58" y="60" width="200" height="155" rx="6" fill="#eef1f7"/></svg>
    <div class="label">Lorem ipsum</div><div class="rule"></div>
  </div>
  <div class="product" style="left:442px">
    <svg width="316" height="275" viewBox="0 0 316 275"><polygon points="79,1 237,1 315,137.5 237,274 79,274 1,137.5" fill="#fff" stroke="#bbb" stroke-width="1.2"/><rect role="img" aria-label="Two aspiration needles, one blue and one green, lying diagonally" x="58" y="60" width="200" height="155" rx="6" fill="#eef1f7"/></svg>
    <div class="label">Lorem ipsum</div><div class="rule"></div>
  </div>
  <div class="product" style="left:794px">
    <svg width="316" height="275" viewBox="0 0 316 275"><polygon points="79,1 237,1 315,137.5 237,274 79,274 1,137.5" fill="#fff" stroke="#bbb" stroke-width="1.2"/><rect role="img" aria-label="Blue handled aspiration device with stylet and trocar" x="58" y="60" width="200" height="155" rx="6" fill="#eef1f7"/></svg>
    <div class="label">Lorem ipsum</div><div class="rule"></div>
  </div>
</section>

<section class="team">
  <h2 class="title">Our Team</h2>
  <svg width="0" height="0" class="abs"><defs><symbol id="star" viewBox="0 0 12 12"><path d="M6 0l1.8 4 4.2.4-3.2 2.8 1 4.2L6 9.2 2.2 11.4l1-4.2L0 4.4 4.2 4z" fill="#f5c518"/></symbol></defs></svg>

  <div class="member" style="left:66px">
    <div class="photo" role="img" aria-label="Portrait of a female doctor in a white coat"></div>
    <h4>Dr A.Mirel</h4>
    <div class="stars"><svg width="12" height="12"><use href="#star"/></svg><svg width="12" height="12"><use href="#star"/></svg><svg width="12" height="12"><use href="#star"/></svg><svg width="12" height="12"><use href="#star"/></svg><svg width="12" height="12"><use href="#star"/></svg></div>
    <p>Lorem ipsum dolor sit amet, consectetur adipiscing elit, sed do eiusmod tempor incididun</p>
    <em>(Lorem ipsum dolor sit ame)</em>
  </div>
  <div class="member" style="left:334px">
    <div class="photo" role="img" aria-label="Portrait of a male doctor with a stethoscope"></div>
    <h4>Dr Tobin Vale</h4>
    <div class="stars"><svg width="12" height="12"><use href="#star"/></svg><svg width="12" height="12"><use href="#star"/></svg><svg width="12" height="12"><use href="#star"/></svg><svg width="12" height="12"><use href="#star"/></svg><svg width="12" height="12"><use href="#star"/></svg></div>
    <p>Lorem ipsum dolor sit amet, consectetur adipiscing elit, sed do eiusmod tempor incididun</p>
    <em>(Lorem ipsum dolor sit ame)</em>
  </div>
  <div class="member" style="left:604px">
    <div class="photo" role="img" aria-label="Portrait of a female doctor with a stethoscope"></div>
    <h4>Dr Lena Frost</h4>
    <div class="stars"><svg width="12" height="12"><use href="#star"/></svg><svg width="12" height="12"><use href="#star"/></svg><svg width="12" height="12"><use href="#star"/></svg><svg width="12" height="12"><use href="#star"/></svg><svg width="12" height="12"><use href="#star"/></svg></div>
    <p>Lorem ipsum dolor sit amet, consectetur adipiscing elit, sed do eiusmod tempor incididun</p>
    <em>(Lorem ipsum dolor sit ame)</em>
  </div>
  <div class="member" style="left:873px">
    <div class="photo" role="img" aria-label="Portrait of a smiling female doctor"></div>
    <h4>Dr R.Oskaro</h4>
    <div class="stars"><svg width="12" height="12"><use href="#star"/></svg><svg width="12" height="12"><use href="#star"/></svg><svg width="12" height="12"><use href="#star"/></svg><svg width="12" height="12"><use href="#star"/></svg><svg width="12" height="12"><use href="#star"/></svg></div>
    <p>Lorem ipsum dolor sit amet, consectetur adipiscing elit, sed do eiusmod tempor incididun</p>
    <em>(Lorem ipsum dolor sit ame)</em>
  </div>

  <div class="btn">View All Team Members</div>
</section>

<section class="faq">
  <h2 class="title">Frequently Asked Questions</h2>
  <div class="faq-item" style="top:180px">
    <h5>Lorem ipsum dolor sit amet, consectetur adipiscing elit, sed do eiusmod?</h5>
    <p>Sed ut perspiciatis unde omnis iste natus error sit voluptatem accusantium doloremque laudantium, totam rem aperiam, eaque ipsa quae ab illo inventore veritatis et quasi architecto</p>
  </div>
  <div class="faq-item" style="top:340px">
    <h5>Lorem ipsum dolor sit amet, consectetur adipiscing elit, sed do eiusmod?</h5>
    <p>Sed ut perspiciatis unde omnis iste natus error sit voluptatem accusantium doloremque laudantium, totam rem aperiam, eaque ipsa quae ab illo inventore veritatis et quasi architecto</p>
  </div>
  <div class="faq-item" style="top:506px">
    <h5>Lorem ipsum dolor sit amet, consectetur adipiscing elit, sed do eiusmod?</h5>
    <p>Sed ut perspiciatis unde omnis iste natus error sit voluptatem accusantium doloremque laudantium, totam rem aperiam, eaque ipsa quae ab illo inventore veritatis et quasi architecto</p>
  </div>
  <div class="btn">View All</div>
</section>

<section class="newsletter">
  <h6 class="abs">Subscribe our Newsletter</h6>
  <div class="abs sub">Sed ut perspiciatis unde omnis</div>
  <div class="abs field">Enter Your Email Address</div>
  <div class="abs send"><svg width="20" height="20" viewBox="0 0 24 24"><path d="M22 2L2 10l7 3 3 7z M9 13l13-11" fill="none" stroke="#fff" stroke-width="1.8" stroke-linejoin="round"/></svg></div>
</section>

<footer class="site-footer">
  <div class="abs pin"><svg width="16" height="20" viewBox="0 0 16 20"><path d="M8 0a7 7 0 0 0-7 7c0 5 7 13 7 13s7-8 7-13a7 7 0 0 0-7-7z" fill="#fff"/><circle cx="8" cy="7" r="2.6" fill="#f07022"/></svg></div>
  <div class="abs address">48 Harlow Lane Suite B<br>Brenfield, Ontario<br>Phone: +1 555 789 0145</div>
  <nav class="abs foot-nav"><span>Home</span><span>Products</span><span>Providers</span><span>Resources</span><span>Distributors</span><span>FAQ</span><span>Contact</span></nav>
  <div class="abs social"><span></span><span></span><span></span><span></span><span></span></div>
  <div class="abs center copy">© 2019 Copyrights.All Rights Reserved</div>
</footer>

</body>
</html>
```